Environmental Consultancey needs Web Design

A consultancey firm based in Papua New Guinea specialising servicing a client market primarily in Melanesia, the wider Pacific Region and South East Asia. The firm provides services to community development and resource extraction activites that incorporate sustainable livelihoods for local customary land owners with environmentally responsibile practices and a focus on maintaining biodiversity and ecosystem services. We aim to encompass Culture, Custom and Science in our approach. Our website preferentially will convey a relaxed Pacific Island feel in its colours and design rather than a sterile corporate feel. See attached logo that will need to be visible on page or which may provide basis for ideas for the page.

Target Market(s)

Our target market is primarily the oil, gas and mining industry, secondarily international donor and aid programs followed by government projects and not for profit programs. Services include:
1. Biodiversity and Conservation - Fauna and Flora survey, assessment, management, monitoring & research, protected areas & endangered & threatend species.
2. Social & Community - impact, stakeholder engagement, census and survey, land and community affairs, capacity building empowerment.
3. Environmental Management - sustainable use, enterprise development & management, biodiversity offsets.

Industry/Entity Type

Community

Requirements
Must have
• Multiple pages, Logo somewhere on home page. Space for a couple of photos that as yet ive not decieded upon.
Nice to have
• Perhaps incorporate shapes, texture and colours that convey a feel of the attached photo of a blue bird of paradise. The blue fine overlapping and interlocking feather patterns are appealing perhaps as a background and the other colours used in boarders ? Abstract is fine as would be symbolic images or tribal ambience. The company is all about blending humanity in all its forms with the environment.

```html
<!DOCTYPE html>
<html lang="en">
<head>
<meta charset="utf-8">
<title>Kaluma Consult</title>
<link rel="stylesheet" href="https://fonts.googleapis.com/css2?family=Open+Sans:wght@400;600&family=Arimo:wght@400&family=Advent+Pro:wght@400&display=swap">
<style>
:root{
  --page-bg:#e3dacb;
  --panel:#f4f1ea;
  --band:#dccdb0;
  --search:#ece6da;
  --ink:#333333;
  --slider-green:#64b681;
  --slider-dot:#4f9968;
  --chev:#b7e35a;
  --rule:#7b8a3b;
  --welcome:#c2b898;
  --footer:#6a8c6c;
  --footer-field:#7fa38a;
  --footer-text:#eef4ec;
  --submit-top:#3cc374;
  --submit-bot:#1f9a50;
  --social-1:#1f79b3;
  --social-2:#39b5e3;
  --social-3:#3a5a98;
  --brand-ink:#333333;
}
*{box-sizing:border-box;margin:0;padding:0}
html,body{width:1077px;height:1200px;overflow:hidden;background:var(--page-bg)}
body{font-family:"Open Sans",sans-serif;color:var(--ink)}
.stage{position:relative;width:1049px;height:1169px;transform:scale(1.0267,1.0265);transform-origin:0 0;overflow:hidden}
.abs{position:absolute}
.sheet{left:23px;top:15px;width:1002px;height:923px;background:linear-gradient(180deg,#fdfcf9 0%,var(--panel) 40%,#e9e3d6 100%)}
.header-band{left:0;top:30px;width:1049px;height:57px;background:var(--band)}
.brand{left:31px;top:28px;width:180px;height:177px;background:#fff;display:flex;align-items:center;justify-content:center}
.brand-name{font-size:20px;font-weight:600;color:var(--brand-ink);text-align:center;line-height:1.25}
.search{left:581px;top:41px;width:221px;height:32px;background:var(--search);font-size:13px;color:#8a8a8a;padding:8px 0 0 16px}
.search svg{position:absolute;right:10px;top:5px}
.follow{left:842px;top:50px;font-size:11px;color:#333}
.social{top:48px;width:20px;height:20px;border-radius:2px}
.s1{left:925px;background:var(--social-1)}
.s2{left:950px;background:var(--social-2)}
.s3{left:976px;background:var(--social-3)}
.nav{left:226px;top:103px;display:flex;width:765px}
.nav-item{width:95.6px;text-align:center}
.nav-tile{height:75px;border-top:12px solid var(--stripe);background:var(--tile);border-radius:0 0 7px 7px;display:flex;align-items:center;justify-content:center}
.nav-label{font-family:"Arimo",sans-serif;font-size:17px;color:var(--label);margin-top:3px}
.slider-shadow{left:150px;top:598px;width:730px;height:22px;border-radius:50%;background:radial-gradient(ellipse at center,rgba(60,60,60,.45),rgba(60,60,60,0) 70%)}
.hero{left:54px;top:237px;width:538px;height:363px;border:2px solid #222;background:radial-gradient(ellipse at 45% 45%,#3a6fd0 0%,#2d5aa8 22%,#2f7a86 48%,#5ea7a0 70%,#2e5a4a 100%);overflow:hidden}
.hero-caption{position:absolute;left:0;bottom:0;width:100%;height:64px;background:rgba(40,40,40,.55);font-family:"Advent Pro",sans-serif;font-size:27px;color:#fff;padding:14px 0 0 18px;letter-spacing:.3px}
.slides{left:592px;top:237px;width:405px;height:363px;background:var(--slider-green);padding:0 14px}
.slide{position:relative;height:88px;border-bottom:2px dotted var(--slider-dot);padding:14px 0 0 39px;color:#fff}
.slide:last-child{border-bottom:0}
.slide h3{font-weight:400;font-size:23px;line-height:1.2}
.slide p{font-size:11.5px;line-height:15px}
.slide svg{position:absolute;left:2px;top:34px}
.rule{left:73px;top:635px;width:902px;height:2px;background:var(--rule)}
.welcome{left:48px;top:668px;width:440px;height:246px;background:var(--welcome);border-radius:8px;padding:14px 37px 0 35px}
.welcome h2{font-weight:400;font-size:25px;color:#fff;margin-left:3px;line-height:1.2}
.welcome p{font-size:12.3px;line-height:17px;text-align:justify;color:#333;margin-top:8px;hyphens:auto;-webkit-hyphens:auto;letter-spacing:.15px}
.projects-title{left:513px;top:656px;font-size:21px;font-weight:400;color:#333}
.thumb{height:107px;border:1px solid #555;background:linear-gradient(135deg,#2f8a86 0%,#3a78c8 45%,#1e4f8a 70%,#4d8a5a 100%)}
.thumb.wide{width:158px}
.thumb.alt{width:146px;background:linear-gradient(135deg,#b8b28a 0%,#2e6aa8 45%,#1a3a5a 70%,#c2a866 100%)}
.footer{left:0;top:938px;width:1049px;height:231px;background:linear-gradient(180deg,#7a9878 0%,var(--footer) 60%,#5f8062 100%);color:var(--footer-text)}
.links{top:30px;font-size:12.5px;line-height:15.5px;list-style:none}
.l1{left:59px}.l2{left:217px}
.contact{left:441px;top:30px;font-size:12.5px;line-height:15.5px}
.form-title{left:708px;top:6px;font-size:12.5px}
.field{left:709px;width:251px;height:30px;background:var(--footer-field);font-size:12.5px;padding:6px 0 0 11px;color:#eef4ec}
.submit{left:888px;top:197px;width:71px;height:26px;background:linear-gradient(180deg,var(--submit-top),var(--submit-bot));color:#fff;font-size:13px;text-align:center;padding-top:3px;border:1px solid #1a8444}
.copyright{left:48px;top:194px;font-size:12.5px}
</style>
</head>
<body>
<svg width="0" height="0" style="position:absolute" aria-hidden="true">
  <symbol id="icon-profile" viewBox="0 0 48 48"><rect x="4" y="4" width="40" height="32" rx="5" fill="none" stroke="#fff" stroke-width="3.5"/><path d="M12 36 L10 45 L20 36" fill="none" stroke="#fff" stroke-width="3.5" stroke-linejoin="round"/><circle cx="24" cy="16" r="5" fill="#fff"/><path d="M14 31 Q24 18 34 31 Z" fill="#fff"/></symbol>
  <symbol id="icon-home" viewBox="0 0 48 48"><path d="M6 22 L24 6 L42 22 M11 19 V42 H37 V19" fill="none" stroke="#fff" stroke-width="3.5" stroke-linejoin="round"/><rect x="19" y="25" width="10" height="10" fill="none" stroke="#fff" stroke-width="3.5"/></symbol>
  <symbol id="icon-chat" viewBox="0 0 48 48"><path d="M20 8 H40 a5 5 0 0 1 5 5 V32 a5 5 0 0 1 -5 5 H28 L22 44 V37 H20 a5 5 0 0 1 -5 -5 V13 a5 5 0 0 1 5 -5 Z" fill="none" stroke="#fff" stroke-width="3.5"/><path d="M9 14 a5 5 0 0 0 -5 5 V30 a5 5 0 0 0 4 5" fill="none" stroke="#fff" stroke-width="3.5"/><path d="M22 18 H38 M22 23 H38 M22 28 H38" stroke="#fff" stroke-width="3"/></symbol>
  <symbol id="icon-chevron" viewBox="0 0 22 26"><path d="M12 2 L3 13 L12 24 M20 2 L11 13 L20 24" fill="none" stroke="var(--chev)" stroke-width="2.2"/></symbol>
</svg>

<div class="stage">
  <div class="abs sheet"></div>
  <div class="abs header-band"></div>

  <div class="abs brand"><span class="brand-name">Kaluma<br>Consult</span></div>

  <div class="abs search">Search
    <svg width="30" height="24" viewBox="0 0 30 24"><circle cx="11" cy="10" r="7" fill="none" stroke="#777" stroke-width="2.5"/><path d="M16 15 L26 22" stroke="#777" stroke-width="3.5" stroke-linecap="round"/></svg>
  </div>
  <div class="abs follow">Follow Us on :</div>
  <span class="abs social s1"></span><span class="abs social s2"></span><span class="abs social s3"></span>

  <nav class="abs nav">
    <div class="nav-item" style="--tile:#5cb5ae;--stripe:#3a9a92;--label:#1f6b66"><div class="nav-tile"><svg width="46" height="46"><use href="#icon-profile"/></svg></div><div class="nav-label">Button 2</div></div>
    <div class="nav-item" style="--tile:#80d0c8;--stripe:#4db0a8;--label:#4aa39c"><div class="nav-tile"><svg width="46" height="46"><use href="#icon-home"/></svg></div><div class="nav-label">Button 3</div></div>
    <div class="nav-item" style="--tile:#5bb3ab;--stripe:#3e9c94;--label:#1d6a64"><div class="nav-tile"><svg width="46" height="46"><use href="#icon-profile"/></svg></div><div class="nav-label">Button 4</div></div>
    <div class="nav-item" style="--tile:#3f9590;--stripe:#1f6e6a;--label:#174a48"><div class="nav-tile"><svg width="46" height="46"><use href="#icon-chat"/></svg></div><div class="nav-label">Button 5</div></div>
    <div class="nav-item" style="--tile:#8aac28;--stripe:#6b8a10;--label:#6b8a10"><div class="nav-tile"><svg width="46" height="46"><use href="#icon-home"/></svg></div><div class="nav-label">Button 6</div></div>
    <div class="nav-item" style="--tile:#7a9a2a;--stripe:#5a7a16;--label:#5a7a16"><div class="nav-tile"><svg width="46" height="46"><use href="#icon-profile"/></svg></div><div class="nav-label">Button 7</div></div>
    <div class="nav-item" style="--tile:#6c7f32;--stripe:#4a5e1a;--label:#3f4f14"><div class="nav-tile"><svg width="46" height="46"><use href="#icon-chat"/></svg></div><div class="nav-label">Button 8</div></div>
    <div class="nav-item" style="--tile:#7f9a30;--stripe:#5a7a16;--label:#4f6414"><div class="nav-tile"><svg width="46" height="46"><use href="#icon-profile"/></svg></div><div class="nav-label">Button 9</div></div>
  </nav>

  <div class="abs slider-shadow"></div>
  <div class="abs hero" role="img" aria-label="Photograph of a blue bird of paradise hanging from a branch">
    <div class="hero-caption">" Encompassing Culture, Custom &amp; Science "</div>
  </div>

  <div class="abs slides">
    <div class="slide"><svg width="22" height="26"><use href="#icon-chevron"/></svg><h3>Slider 1</h3><p>The atmosphere of the Earth serves as a key factor in sustaining the planetary ecosystem.</p></div>
    <div class="slide"><svg width="22" height="26"><use href="#icon-chevron"/></svg><h3>Slider 2</h3><p>The atmosphere of the Earth serves as a key factor in sustaining the planetary ecosystem.</p></div>
    <div class="slide"><svg width="22" height="26"><use href="#icon-chevron"/></svg><h3>Slider 3</h3><p>The atmosphere of the Earth serves as a key factor in sustaining the planetary ecosystem.</p></div>
    <div class="slide"><svg width="22" height="26"><use href="#icon-chevron"/></svg><h3>Slider 4</h3><p>The atmosphere of the Earth serves as a key factor in sustaining the planetary ecosystem.</p></div>
  </div>

  <div class="abs rule"></div>

  <section class="abs welcome">
    <h2>Welcome!</h2>
    <p>The potential dangers of global warming are being increasingly studied by a wide global consortium of scientists. These scientists are increasingly concerned about the potential long-term effects of global warming on our natural environment and on the planet. Of particular concern is how climate change and global warming caused by anthropogenic, or human-made releases of greenhouse gases, most notably carbon dioxide, can act interactively, and have adverse effects upon the planet, its natural environment and humans' existence.</p>
  </section>

  <h2 class="abs projects-title">Our Projects</h2>
  <div class="abs thumb wide" style="left:519px;top:693px" role="img" aria-label="Project photo: blue bird of paradise"></div>
  <div class="abs thumb alt" style="left:683px;top:693px" role="img" aria-label="Project photo: bird of paradise on a branch"></div>
  <div class="abs thumb wide" style="left:835px;top:693px" role="img" aria-label="Project photo: blue bird of paradise"></div>
  <div class="abs thumb wide" style="left:519px;top:805px" role="img" aria-label="Project photo: blue bird of paradise"></div>
  <div class="abs thumb alt" style="left:683px;top:805px" role="img" aria-label="Project photo: bird of paradise on a branch"></div>
  <div class="abs thumb wide" style="left:835px;top:805px" role="img" aria-label="Project photo: blue bird of paradise"></div>

  <footer class="abs footer">
    <ul class="abs links l1"><li>Button 1</li><li>Button 2</li><li>Button 3</li><li>Button 4</li><li>Button 5</li><li>Button 6</li><li>Button 7</li><li>Button 8</li></ul>
    <ul class="abs links l2"><li>Button 1</li><li>Button 2</li><li>Button 3</li><li>Button 4</li><li>Button 5</li><li>Button 6</li><li>Button 7</li><li>Button 8</li></ul>
    <div class="abs contact">Contact Info<br>Addres Details<br>Telephone No.<br>Fax No.<br>Email id:</div>
    <div class="abs form-title">Queries / Comments</div>
    <div class="abs field" style="top:29px">Name</div>
    <div class="abs field" style="top:64px">Contact No.</div>
    <div class="abs field" style="top:100px">Email id</div>
    <div class="abs field" style="top:136px;height:56px;padding-top:4px">Comments</div>
    <div class="abs submit">Submit</div>
    <div class="abs copyright">Copyright All right reserved</div>
  </footer>
</div>
</body>
</html>
```